Business cards to launch an education platform

Hi,
I am looking at having new business cards designed.
I am a startup, developing a web platform for schools and university, the education world. It's an online assessment system.
I would like a card that looks classy, and that is using the colors and the font of my logo.

I have attached:
1) my logo
2) A business card that I have designed quickly so you can have all the information required in the card, but I really don't like it.
3) The font that I am using (Lato Regular) to design my web platform
4) Some screenshots of my web platform so you can have a look at the style that I have.

Target Market(s)

Major market: Education system: Schools and university
Minor markets: Business in general

Industry/Entity Type

Business

Contact Information for Business Card

Clara Fenwick
Director

M: 0437 518 902
E: clara.fenwick@amberLoomSystems.com.au

Requirements
Must have
• The colors of my logo

```html
<!DOCTYPE html>
<html lang="en">
<head>
<meta charset="utf-8">
<title>Amber Loom Systems – Business Card</title>
<link rel="stylesheet" href="https://fonts.googleapis.com/css2?family=Lato:wght@400;700&display=swap">
<style>
  :root {
    --backdrop: #d8d4cd;
    --card: #eef0f2;
    --navy: #1c3350;
    --brand-blue: #1d4f8a;
    --accent-blue: #2a8fc4;
    --ink: #2b2f36;
  }
  * { margin: 0; padding: 0; box-sizing: border-box; }
  html, body {
    width: 1200px;
    height: 969px;
    overflow: hidden;
    background: var(--backdrop);
    font-family: "Lato", sans-serif;
  }
  .canvas {
    position: relative;
    width: 1200px;
    height: 969px;
  }
  .business-card {
    position: absolute;
    left: 100px;
    top: 206px;
    width: 1000px;
    height: 556px;
    background: var(--card);
    border-radius: 6px;
    box-shadow: 0 10px 30px rgba(0, 0, 0, 0.12);
    overflow: hidden;
  }
  .company-name {
    position: absolute;
    left: 56px;
    top: 66px;
    color: var(--navy);
    font-weight: 400;
    font-size: 58px;
    line-height: 1.05;
    letter-spacing: 4px;
  }
  .company-name span { display: block; }
  .company-name .secondary {
    color: var(--accent-blue);
    font-size: 44px;
    letter-spacing: 3px;
  }
  .brand-square {
    position: absolute;
    left: 560px;
    top: 36px;
    width: 410px;
    height: 410px;
    background: var(--brand-blue);
  }
  .accent-bar {
    position: absolute;
    left: 4px;
    top: 344px;
    width: 14px;
    height: 160px;
    background: var(--navy);
  }
  .contact {
    position: absolute;
    left: 56px;
    top: 336px;
  }
  .contact-name {
    color: var(--navy);
    font-weight: 700;
    font-size: 34px;
    letter-spacing: 1px;
    line-height: 1.2;
  }
  .contact-role {
    color: var(--accent-blue);
    font-weight: 400;
    font-size: 27px;
    letter-spacing: 1px;
    margin-top: 4px;
  }
  .contact-list {
    list-style: none;
    margin-top: 18px;
  }
  .contact-list li {
    display: flex;
    align-items: center;
    gap: 14px;
    color: var(--ink);
    font-size: 25px;
    line-height: 38px;
    white-space: nowrap;
  }
  .contact-list svg {
    width: 24px;
    height: 24px;
    flex: none;
  }
</style>
</head>
<body>
<main class="canvas">
  <section class="business-card">
    <h1 class="company-name">
      <span>AMBER LOOM</span>
      <span class="secondary">Systems</span>
    </h1>
    <div class="brand-square" aria-hidden="true"></div>

    <div class="accent-bar"></div>
    <div class="contact">
      <p class="contact-name">CLARA FENWICK</p>
      <p class="contact-role">DIRECTOR</p>
      <ul class="contact-list">
        <li>
          <svg viewBox="0 0 24 24" aria-hidden="true">
            <rect x="6" y="2" width="12" height="20" rx="2" fill="none" stroke="#2b2f36" stroke-width="2"/>
            <line x1="10" y1="18" x2="14" y2="18" stroke="#2b2f36" stroke-width="2"/>
          </svg>
          <span>0437 518 902</span>
        </li>
        <li>
          <svg viewBox="0 0 24 24" aria-hidden="true">
            <rect x="2" y="6" width="20" height="13" fill="#2b2f36"/>
            <polyline points="2,6 12,13 22,6" fill="none" stroke="#eef0f2" stroke-width="1.6"/>
          </svg>
          <span>clara.fenwick@amberLoomSystems.com.au</span>
        </li>
      </ul>
    </div>
  </section>
</main>
</body>
</html>
```